PostCard Design Project

I am making a mailing postcard
I am having the mailing printed using 4 color foil on certain parts.
I am looking for a design that maximizes the foil process where certain parts are done in foil to grab the customers attention (example: if there is a car on the postcard the headlights would be done in foil) .
I am targeting some industries, (auto, real estate, medical, beauty) I would like the post card to have examples of postcard ideas for 2 or 3 of these industries.
specs:
the postcard should be atleast 6.5x9 up to 8.5x11, I don't want to restrict the space for the creative as I don't want everything to look like a huge mess. both sides will be used.
the piece is a direct mail piece so it has to meet requirements of https://www.mailvantor.com/business/pdf/quick-reference-guide.pdf
text will be
"business with no limits, meet mailing with no addresses, gain new customers through "Open Porch Route Drop" reach new customers at their home without needing their address. "
I also want some current print specials I am running included.
-double your order FREE (order 500 business cards and get 1000)
-250 100lb gloss stock brochures 99.00
-business packages (cards, envelopes and letterhead) 299
-1000 flyers 140.40
-5000 postcards 179.99
A list of services
banners
booklets
brochures
business cards
calendars
catalogs
CD/DVD packages
envelopes
event tickets
flyers
hangtags
postcards
posters
presentation folders
rack cards
labels
table tents
window cling and decal
"order 24/7 orders@inkwillow.com" must be included
my logo is InkWillow will be supplied later
ive received some great designs. however Im looking for something a little more modern like some zorvel would put out. if the amount of words is too much please feel free to edit. also an idea i had for the list of services i offer is to have it transparent yet readable as the background of the postcard some small some big but covering the entire backgroud. you can then design on top of that with other thing. just an early morning thought
Reason: I have uploaded a sketch of my idea, please take time to look at it for an accurate depiction of what im looking for. feel free to add elements that make it pop off the page
Reason: We are getting close i will be providing feed back today

```html
<!DOCTYPE html>
<html lang="en">
<head>
<meta charset="utf-8">
<title>InkWillow Postcard</title>
<link rel="stylesheet" href="https://fonts.googleapis.com/css2?family=Anton&family=Open+Sans:wght@400;600;700&display=swap">
<style>
  :root {
    --page: #e9e6e1;
    --card-black: #050505;
    --card-dark: #161616;
    --lime: #d3de3c;
    --sky: #2ba4e4;
    --white: #ffffff;
    --strip-top: #8d8d8d;
    --strip-bottom: #3a3a3a;
    --jewel-tone: #8e8f93;
    --car-tone: #c4161c;
    --portrait-tone: #d9c4b4;
  }
  * { margin: 0; padding: 0; box-sizing: border-box; }
  html, body { width: 1200px; height: 900px; overflow: hidden; }
  body { background: var(--page); position: relative; font-family: "Open Sans", sans-serif; }

  .postcard {
    position: absolute;
    left: 285px;
    width: 630px;
    height: 420px;
    overflow: hidden;
    background: linear-gradient(160deg, var(--card-dark), var(--card-black) 60%);
    box-shadow: 0 6px 18px rgba(0,0,0,.25);
  }
  .postcard--front { top: 20px; }
  .postcard--back { top: 460px; }

  .footer-strip {
    position: absolute; left: 0; right: 0; bottom: 0; height: 40px;
    background: linear-gradient(180deg, var(--strip-top), var(--strip-bottom));
  }

  /* Front */
  .showcase { position: absolute; }
  .showcase--jewelry { left: 250px; top: 22px; width: 170px; height: 230px;
    background: linear-gradient(160deg, #b7b8bc, var(--jewel-tone) 55%, #4a4b4f); }
  .showcase--auto { left: 400px; top: 110px; width: 215px; height: 175px;
    background: linear-gradient(200deg, #e5e5e5 0%, var(--car-tone) 35%, #5a0b0e 100%); }
  .showcase--beauty { left: 420px; top: 0; width: 195px; height: 112px;
    background: linear-gradient(90deg, #f1f1f1 0%, var(--portrait-tone) 45%, #8a6a55 100%); }

  .headline {
    position: absolute; left: 24px; top: 118px;
    font-family: "Anton", sans-serif; color: var(--white);
    line-height: 1.02; letter-spacing: .5px; text-transform: uppercase;
  }
  .headline__line { display: block; font-size: 34px; }
  .headline__line--shine { font-size: 60px; line-height: 1.05; }
  .headline .accent { color: var(--lime); }

  .order-line {
    position: absolute; left: 24px; top: 318px;
    color: var(--sky); font-weight: 700; font-size: 19px; line-height: 1.15;
  }

  .brand-mark {
    position: absolute; font-weight: 700; letter-spacing: 1px; text-transform: uppercase;
    white-space: nowrap;
  }
  .postcard--front .brand-mark { right: 26px; top: 316px; font-size: 28px; color: var(--lime); }

  .route-drop {
    position: absolute; left: 24px; right: 24px; bottom: 0; height: 40px;
    display: flex; align-items: center; justify-content: center;
    color: var(--white); font-size: 12px; font-weight: 600; text-align: center;
  }
  .route-drop strong { font-weight: 600; }

  /* Back */
  .service-cloud {
    position: absolute; left: 16px; top: 10px; list-style: none;
    line-height: .98; font-weight: 400; color: var(--white);
  }
  .service-cloud li { white-space: nowrap; }
  .service--sky { color: var(--sky); }
  .service--lime { color: var(--lime); }

  .stamp-box { position: absolute; right: 28px; top: 18px; width: 58px; height: 44px; background: var(--white); }
  .address-box { position: absolute; left: 330px; top: 48px; width: 200px; height: 150px; background: var(--white); }

  .postcard--back .brand-mark--primary { left: 300px; top: 210px; font-size: 30px; color: var(--lime); }
  .postcard--back .brand-mark--small { left: 330px; top: 16px; font-size: 18px; color: var(--white); }

  .specials {
    position: absolute; left: 330px; top: 258px; width: 280px; list-style: none;
    color: var(--white); font-weight: 600; font-size: 11.5px; line-height: 1.35; text-align: center;
  }

  .strip-contact {
    position: absolute; right: 18px; bottom: 11px;
    color: var(--white); font-size: 13px; font-weight: 400;
  }
</style>
</head>
<body>

<section class="postcard postcard--front">
  <div class="showcase showcase--jewelry" role="img" aria-label="Jewelry advertisement sample with silver rings"></div>
  <div class="showcase showcase--auto" role="img" aria-label="Auto advertisement sample with a red sports car front"></div>
  <div class="showcase showcase--beauty" role="img" aria-label="Beauty advertisement sample with a smiling model"></div>

  <h1 class="headline">
    <span class="headline__line">Printing</span>
    <span class="headline__line">That <span class="accent">Makes</span></span>
    <span class="headline__line">Your <span class="accent">Business</span></span>
    <span class="headline__line headline__line--shine">Shine !</span>
  </h1>

  <p class="order-line">24 hr/7 Day<br>orders@inkwillow.com</p>

  <div class="brand-mark">InkWillow</div>
  <div class="footer-strip"></div>
  <p class="route-drop">Reach new customers at home without their address through "<strong>Open Porch Route Drop</strong>"</p>
</section>

<section class="postcard postcard--back">
  <ul class="service-cloud">
    <li class="service--sky" style="font-size:12px">Banner</li>
    <li style="font-size:13px">booklets</li>
    <li style="font-size:14px">brochures</li>
    <li class="service--lime" style="font-size:14px">Business cards</li>
    <li style="font-size:20px">Calendars</li>
    <li style="font-size:23px">Catalogs</li>
    <li class="service--sky" style="font-size:34px">Envelopes</li>
    <li style="font-size:18px">Presentation Folder</li>
    <li class="service--lime" style="font-size:32px">Event Tickets</li>
    <li style="font-size:18px">Window cling and Decal</li>
    <li style="font-size:20px">CD/DVD Packages</li>
    <li class="service--lime" style="font-size:32px">rack Cards</li>
    <li style="font-size:24px">Table tents</li>
    <li class="service--sky" style="font-size:34px">Flyers</li>
    <li style="font-size:18px">Hangtags</li>
    <li class="service--lime" style="font-size:15px">postcard</li>
    <li style="font-size:13px">Posters</li>
  </ul>

  <div class="brand-mark brand-mark--small">InkWillow</div>
  <div class="stamp-box"></div>
  <div class="address-box"></div>

  <div class="brand-mark brand-mark--primary">InkWillow</div>

  <ul class="specials">
    <li>Double your order FREE</li>
    <li>(order 500 business cards and get 1000)</li>
    <li>250 100lb gloss stock brochures 99.00</li>
    <li>Business packages</li>
    <li>(cards, envelopes and letterhead) 299</li>
    <li>1000 flyers 140.40</li>
    <li>5000 postcards 179.99</li>
  </ul>

  <div class="footer-strip"></div>
  <p class="strip-contact">24 hr/7 Day orders@inkwillow.com</p>
</section>

</body>
</html>
```